Company Profile for Academic and Study Abroad Services

I am looking for Power Point Design for company Profile . the company is academic and study abroad services. you can visit the website which is www.korvapath.ae . the colour i prefer is Dark Blue + White + Black . you can find all the content for power point and logo and some picture i need you to add it.

Target Market(s)

Students who wants to study abroad. Universities . Learning centre.

Industry/Entity Type

Education

Font styles to use
Serif
Sans Serif

Colors
0555a3
ffffff
000000
aaaaaa

Requirements
Must have
• Must Have Images for each slides.
Nice to have
• infographic. Images related to the study abroad

```html
<!DOCTYPE html>
<html lang="en">
<head>
<meta charset="utf-8">
<title>Korva Path – Company Profile Slides</title>
<link href="https://fonts.googleapis.com/css2?family=Open+Sans:wght@300;400;600;700&family=Oswald:wght@500&display=swap" rel="stylesheet">
<style>
:root{
  --stage-light:#7d7d80;
  --stage-dark:#55565b;
  --slide-bg:#f7f7f8;
  --bar:#43444d;
  --number-box:#0a10a3;
  --brand-blue:#0a3f85;
  --title-blue:#1f3fa6;
  --accent-yellow:#f6c21c;
  --icon-grey:#cfd0d3;
  --text:#1c1c1f;
  --white:#ffffff;
  --step-1:#cbcbcf;
  --step-2:#a9a9ae;
  --step-3:#6e6e74;
  --chart-fill:#6f8db6;
  --cyan:#25c4d8;
  --red:#ec5050;
  --light-grey:#d9dadd;
  --closing-bg:#45464e;
}
*{margin:0;padding:0;box-sizing:border-box}
html,body{width:1200px;height:1200px;overflow:hidden}
body{
  background:linear-gradient(90deg,var(--stage-light),var(--stage-dark));
  font-family:"Open Sans",Arial,sans-serif;color:var(--text);position:relative;
}
.slide{position:absolute;width:538px;height:304px;background:var(--slide-bg);overflow:hidden}
.col-left{left:52px}.col-right{left:615px;width:540px}
.row-1{top:144px}.row-2{top:472px}.row-3{top:800px}

.slide-header{position:absolute;left:0;top:0;width:100%;height:51px;background:var(--bar)}
.slide-header h2{position:absolute;left:30px;top:16px;font-size:14px;font-weight:700;color:var(--white);letter-spacing:.2px}
.slide-number{position:absolute;right:0;top:0;width:110px;height:51px;background:var(--number-box);color:var(--white);font-size:25px;font-weight:400;text-align:center;line-height:51px}

.brand-tag{position:absolute;display:flex;align-items:center;gap:3px;font-size:7px;font-weight:700;color:var(--brand-blue);letter-spacing:.3px}
.brand-tag .mark{width:8px;height:8px;background:currentColor}
.brand-tag.corner{right:14px;bottom:12px}
.brand-tag.on-dark{color:var(--white)}

/* cover */
.cover-photo{position:absolute;left:88px;top:0;right:0;bottom:0;background:linear-gradient(160deg,#8fa5d4 0%,#4f67a6 45%,#1e2d60 100%)}
.cover-band{position:absolute;left:0;top:0}
.cover-title{position:absolute;left:90px;top:50px;color:var(--title-blue);font-weight:700;font-size:12px;line-height:15px}
.cover .brand-tag{left:20px;top:40px;width:44px;flex-direction:column;gap:2px;text-align:center;font-size:7px;line-height:8px}
.cover .brand-tag .mark{width:10px;height:10px}

/* who we are */
.feature{position:absolute;width:110px}
.feature .num{position:absolute;left:52px;top:-8px;font-family:"Oswald",Impact,sans-serif;font-weight:500;font-size:46px;line-height:1;color:var(--accent-yellow)}
.feature svg{position:absolute;left:0;top:0}
.feature p{position:absolute;left:0;top:50px;width:118px;font-size:6px;font-weight:700;line-height:7.5px}
.f1{left:41px;top:89px}.f2{left:176px;top:89px}.f3{left:41px;top:193px}.f4{left:176px;top:193px}
.divider{position:absolute;left:337px;top:67px;width:1px;height:219px;background:#c9c9cc}
.headline{position:absolute;left:362px;top:88px;width:160px}
.headline h3{font-size:22px;font-weight:400;letter-spacing:.3px;line-height:1}
.headline .sub{font-size:7.5px;font-weight:600;margin-top:2px}
.headline .body{font-size:5.3px;line-height:7px;margin-top:30px}
.headline .body + .body{margin-top:7px}

/* what we do */
.steps{position:absolute;left:84px;top:90px;width:370px;height:123px;display:flex;border-radius:6px;overflow:hidden}
.step{flex:1;position:relative;color:var(--white);text-align:center;padding:24px 12px 0}
.step:nth-child(1){background:var(--step-1)}
.step:nth-child(2){background:var(--step-2)}
.step:nth-child(3){background:var(--step-3)}
.step h4{font-size:18px;font-weight:300;letter-spacing:.3px}
.step p{font-size:4.8px;line-height:6.4px;margin-top:4px}
.step:not(:last-child)::after{content:"";position:absolute;right:-6px;top:52px;border-left:6px solid;border-top:6px solid transparent;border-bottom:6px solid transparent;z-index:2}
.step:nth-child(1)::after{border-left-color:var(--step-1)}
.step:nth-child(2)::after{border-left-color:var(--step-2)}
.steps-caption{position:absolute;left:82px;top:229px;width:376px;text-align:center;font-size:6.4px;line-height:8.4px;font-weight:600}

/* education levels */
.chart{position:absolute;left:0;top:0}
.chart text{font-family:"Open Sans",Arial,sans-serif;font-size:7.5px;fill:#222}
.legend{position:absolute;top:253px;width:100px;font-size:5.2px;font-weight:600;line-height:6.6px}
.lg1{left:109px}.lg2{left:241px}.lg3{left:374px}

/* why choose */
.choice{position:absolute;top:0;bottom:0;width:50%;color:var(--white);text-align:center}
.choice.a{left:0;background:var(--brand-blue)}
.choice.b{right:0;background:var(--closing-bg)}
.choice-title{position:absolute;left:30px;top:20px;font-size:14px;font-weight:700;color:var(--white);z-index:2}
.choice h3{margin-top:60px;font-size:25px;font-weight:400;letter-spacing:6px}
.choice .sub{font-size:8px;font-weight:600;margin-top:-2px}
.choice .rule{width:64px;height:1px;background:rgba(255,255,255,.7);margin:10px auto 18px}
.choice .body{width:186px;margin:0 auto;font-size:5.6px;line-height:7.2px}
.choice .body + .body{margin-top:7px}

/* closing */
.closing{background:var(--closing-bg);color:var(--white);text-align:center}
.closing-bg{position:absolute;inset:0;background:linear-gradient(135deg,#4a4b53,#3f4048)}
.closing h2{position:relative;margin-top:46px;font-size:40px;font-weight:400;line-height:38px}
.closing .tagline{position:relative;margin-top:20px;font-size:16.5px;font-weight:400}
.closing .contact{position:relative;margin-top:6px;font-size:6px;line-height:8.4px;font-weight:600}
.closing .social{position:relative;margin-top:9px;font-size:6px;line-height:8.4px;font-weight:600}
</style>
</head>
<body>

<!-- Cover -->
<section class="slide col-left row-1 cover">
  <div class="cover-photo" role="img" aria-label="Blue-toned photograph of a group of smiling university students"></div>
  <svg class="cover-band" width="538" height="304" viewBox="0 0 538 304" aria-hidden="true">
    <polygon points="0,0 88,0 88,24 312,24 268,88 88,88 88,304 0,304" fill="#ffffff"/>
  </svg>
  <div class="brand-tag"><span class="mark"></span>KORVA PATH</div>
  <div class="cover-title">KORVA PATH<br>Universities Entrance Services</div>
</section>

<!-- Who we are -->
<section class="slide col-right row-1">
  <header class="slide-header"><h2>WHO WE ARE</h2><div class="slide-number">01</div></header>

  <div class="feature f1">
    <svg width="44" height="36" viewBox="0 0 44 36" aria-hidden="true">
      <rect x="0" y="22" width="8" height="14" fill="#cfd0d3"/><rect x="11" y="14" width="8" height="22" fill="#cfd0d3"/><rect x="22" y="6" width="8" height="30" fill="#cfd0d3"/><rect x="33" y="0" width="8" height="36" fill="#cfd0d3"/>
    </svg>
    <span class="num">01</span>
    <p>Lorem ipsum dolor sit amet, dicit mellus consetetur ut eum, vim probo libris dicunt at.</p>
  </div>
  <div class="feature f2">
    <svg width="40" height="40" viewBox="0 0 40 40" aria-hidden="true">
      <g fill="#cfd0d3"><circle cx="20" cy="20" r="13"/>
        <rect x="16" y="1" width="8" height="38"/><rect x="1" y="16" width="38" height="8"/>
        <rect x="16" y="1" width="8" height="38" transform="rotate(45 20 20)"/><rect x="16" y="1" width="8" height="38" transform="rotate(-45 20 20)"/></g>
      <circle cx="20" cy="20" r="6" fill="#f7f7f8"/>
    </svg>
    <span class="num">02</span>
    <p>Lorem ipsum dolor sit amet, dicit mellus consetetur ut eum, vim probo libris dicunt at.</p>
  </div>
  <div class="feature f3">
    <svg width="44" height="40" viewBox="0 0 44 40" aria-hidden="true">
      <circle cx="22" cy="11" r="10" fill="#cfd0d3"/><path d="M2 40 Q2 22 22 22 Q42 22 42 40 Z" fill="#cfd0d3"/>
    </svg>
    <span class="num">03</span>
    <p>Lorem ipsum dolor sit amet, dicit mellus consetetur ut eum, vim probo libris dicunt at.</p>
  </div>
  <div class="feature f4">
    <svg width="42" height="40" viewBox="0 0 42 40" aria-hidden="true">
      <circle cx="16" cy="16" r="12" fill="none" stroke="#cfd0d3" stroke-width="6"/><line x1="25" y1="25" x2="38" y2="37" stroke="#cfd0d3" stroke-width="7" stroke-linecap="round"/>
    </svg>
    <span class="num">04</span>
    <p>Lorem ipsum dolor sit amet, dicit mellus consetetur ut eum, vim probo libris dicunt at.</p>
  </div>

  <div class="divider"></div>
  <div class="headline">
    <h3>HEADLINE</h3>
    <p class="sub">Lorem Ipsum Dolor Sit Amet</p>
    <p class="body">Lorem ipsum dolor sit amet, ius exerci corpora eu. Per ne meis vocent iudicabit, in oratio graeci atomorum vim, vide habemus docendi ut eam. Cu dolor salutatus efficiendi nam. Debet quaeque nec te. Omittam reprehendunt eu mea, vocent aperiri eum et, ut ius summo dignissim. Pro ne ubique voluptaria, te alia lorem perfecto vix.</p>
    <p class="body">Nam dolor latine ornatus id, choro partiendo mei et. Idque facer vidisse id nec, constituam dissentiunt per ex. In nam elitr assueverit, eum te nemore menitum hendrerit. Eu solum debet minimum qui. Maluisset gloriatur ne eum, usu et dolor clita adversarium. Ex postea petentium comprehensam vel, vim te eligendi intellegat.</p>
  </div>
  <div class="brand-tag corner"><span class="mark"></span>KORVA PATH</div>
</section>

<!-- What we do -->
<section class="slide col-left row-2">
  <header class="slide-header"><h2>WHAT WE DO</h2><div class="slide-number">02</div></header>
  <div class="steps">
    <div class="step"><h4>STEP 1</h4><p>Meet an advisor to discuss goals, grades, budget and preferred destinations.</p></div>
    <div class="step"><h4>STEP 2</h4><p>Shortlist universities and prepare transcripts, essays and references together.</p></div>
    <div class="step"><h4>STEP 3</h4><p>Submit applications, secure the offer and plan the visa and travel.</p></div>
  </div>
  <p class="steps-caption">Lorem ipsum dolor sit amet, ius exerci corpora eu. Per ne meis vocent iudicabit, in oratio graeci atomorum vim, vide habemus docendi ut eam. Cu dolor salutatus efficiendi nam. Debet quaeque nec te. Omittam reprehendunt eu mea, vocent aperiri eum et, ut ius summo dignissim. Pro ne ubique voluptaria, te alia lorem perfecto vix.</p>
  <div class="brand-tag corner"><span class="mark"></span>KORVA PATH</div>
</section>

<!-- Education levels -->
<section class="slide col-right row-2">
  <header class="slide-header"><h2>EDUCATION LEVELS</h2><div class="slide-number">03</div></header>
  <svg class="chart" width="540" height="304" viewBox="0 0 540 304" aria-label="Area chart of education levels from A to L">
    <path d="M84 166.5 L120 145 L156 160.3 L192 149.6 L228 138.9 L264 157.3 L300 165 L336 154.2 L372 138.9 L408 118.9 L444 131.2 L480 108.2 L480 211 L84 211 Z" fill="#6f8db6"/>
    <g stroke="#c4c6cc" stroke-width=".7" stroke-dasharray="2 2">
      <line x1="84" y1="88" x2="480" y2="88"/><line x1="84" y1="119" x2="480" y2="119"/><line x1="84" y1="149" x2="480" y2="149"/><line x1="84" y1="180" x2="480" y2="180"/>
      <line x1="120" y1="88" x2="120" y2="211"/><line x1="156" y1="88" x2="156" y2="211"/><line x1="192" y1="88" x2="192" y2="211"/><line x1="228" y1="88" x2="228" y2="211"/><line x1="264" y1="88" x2="264" y2="211"/><line x1="300" y1="88" x2="300" y2="211"/><line x1="336" y1="88" x2="336" y2="211"/><line x1="372" y1="88" x2="372" y2="211"/><line x1="408" y1="88" x2="408" y2="211"/><line x1="444" y1="88" x2="444" y2="211"/><line x1="480" y1="88" x2="480" y2="211"/>
    </g>
    <line x1="84" y1="88" x2="84" y2="211" stroke="#888" stroke-width=".8"/>
    <g text-anchor="end"><text x="76" y="91">400</text><text x="76" y="122">300</text><text x="76" y="152">200</text><text x="76" y="183">100</text></g>
    <g text-anchor="middle"><text x="84" y="225">A</text><text x="120" y="225">B</text><text x="156" y="225">C</text><text x="192" y="225">D</text><text x="228" y="225">E</text><text x="264" y="225">F</text><text x="300" y="225">G</text><text x="336" y="225">H</text><text x="372" y="225">I</text><text x="408" y="225">J</text><text x="444" y="225">K</text><text x="480" y="225">L</text></g>
    <rect x="139" y="126" width="35" height="20" fill="#25c4d8"/><polygon points="151,146 161,146 156,152" fill="#25c4d8"/>
    <circle cx="156" cy="160.3" r="2.5" fill="#8d5a5a"/>
    <rect x="282" y="131" width="36" height="21" fill="#ec5050"/><polygon points="295,152 305,152 300,158" fill="#ec5050"/>
    <circle cx="300" cy="165" r="2.5" fill="#8d5a5a"/>
    <rect x="390" y="82" width="36" height="21" fill="#d9dadd"/><polygon points="403,103 413,103 408,109" fill="#d9dadd"/>
    <circle cx="408" cy="118.9" r="2.5" fill="#8d5a5a"/>
    <rect x="84" y="253" width="19" height="19" fill="#25c4d8"/>
    <rect x="216" y="253" width="19" height="19" fill="#ec5050"/>
    <rect x="349" y="253" width="19" height="19" fill="#d9dadd"/>
  </svg>
  <p class="legend lg1">Lorem ipsum dolor sit amet, dicit mellus consetetur ut eum, vim probo libris dicunt at.</p>
  <p class="legend lg2">Lorem ipsum dolor sit amet, dicit mellus consetetur ut eum, vim probo libris dicunt at.</p>
  <p class="legend lg3">Lorem ipsum dolor sit amet, dicit mellus consetetur ut eum, vim probo libris dicunt at.</p>
  <div class="brand-tag corner"><span class="mark"></span>KORVA PATH</div>
</section>

<!-- Why choose -->
<section class="slide col-left row-3">
  <h2 class="choice-title">WHY CHOOSE KORVA PATH</h2>
  <div class="choice a">
    <h3>OPTION A</h3>
    <p class="sub">Lorem Ipsum Dolor Sit Amet</p>
    <div class="rule"></div>
    <p class="body">Lorem ipsum dolor sit amet, ius exerci corpora eu. Per ne meis vocent iudicabit, in oratio graeci atomorum vim, vide habemus docendi ut eam. Cu dolor salutatus efficiendi nam. Debet quaeque nec te. Omittam reprehendunt eu mea, vocent aperiri eum et, ut ius summo dignissim. Pro ne ubique voluptaria, te alia lorem perfecto vix.</p>
    <p class="body">Nam dolor latine ornatus id, choro partiendo mei et. Idque facer vidisse id nec, constituam dissentiunt per ex. In nam elitr assueverit, eum te nemore menitum hendrerit. Eu solum debet minimum qui. Maluisset gloriatur ne eum, usu et dolor clita adversarium. Ex postea petentium comprehensam vel, vim te eligendi intellegat.</p>
  </div>
  <div class="choice b">
    <h3>OPTION B</h3>
    <p class="sub">Lorem Ipsum Dolor Sit Amet</p>
    <div class="rule"></div>
    <p class="body">Lorem ipsum dolor sit amet, ius exerci corpora eu. Per ne meis vocent iudicabit, in oratio graeci atomorum vim, vide habemus docendi ut eam. Cu dolor salutatus efficiendi nam. Debet quaeque nec te. Omittam reprehendunt eu mea, vocent aperiri eum et, ut ius summo dignissim. Pro ne ubique voluptaria, te alia lorem perfecto vix.</p>
    <p class="body">Nam dolor latine ornatus id, choro partiendo mei et. Idque facer vidisse id nec, constituam dissentiunt per ex. In nam elitr assueverit, eum te nemore menitum hendrerit. Eu solum debet minimum qui. Maluisset gloriatur ne eum, usu et dolor clita adversarium. Ex postea petentium comprehensam vel, vim te eligendi intellegat.</p>
  </div>
  <div class="brand-tag corner on-dark"><span class="mark"></span>KORVA PATH</div>
</section>

<!-- Closing -->
<section class="slide col-right row-3 closing">
  <div class="closing-bg" role="img" aria-label="Dark grey background with subtle diagonal stripe texture"></div>
  <h2>THANK<br>YOU</h2>
  <p class="tagline">BE AMONG THE BEST</p>
  <p class="contact">Al Noor Street, Harbor Sports Center<br>Marina Club Suite – 12, 2nd Floor<br>UAE- Abu Dhabi<br>+971 2 555 0142 | +971 50 555 0187 | +971 52 555 0163 | +971 50 555 0129<br>www.korvapath.ae<br>info@korvapath.ae</p>
  <p class="social">Facebook: korvapath.uae<br>Twitter: korvapath_ae<br>Instagram: korvapath.uae</p>
</section>

</body>
</html>
```